Wordpress Theme for Medical Clinics

** Please view updated Sitemap2.pdf doc to clarify some confusion ***

This is a multiuser WordPress subscription site for medical clinics. Please see attachment for sitemap. Please do not include extra content like social media icons, search bars, or images. If you have questions, please ask for clarification.
The site contains the following pages and sub-pages:

1. Home
2. Our Clinic
2a. Our Clinic > Mission
2b. Our Clinic > Services
2c. Our Clinic > Clinic Policies
2d. Our Clinic > Schedules
3. Our Staff
3a. Our Staff > [Staff member page]
4. Resources
4a. Resources > Patient Health (index)
4b. Resources > Patient Health (index) > [post]
4c. Resources > Links
4d. Resources > Forms
5. Alerts
5a. Alerts > [Alert Page]
6. Contact Us

Includes the Following Pages, Subpages, and Content
1. Home
a. About Us
b. Our Staff
c. Bulletins
d. Accepting New Patients (shown as an alert widget)
e. Links
i. Physician Toolbox
ii. Book an Appointment
f. Clinic Policies
i. Show first 3 policies (e.g. Late Arrivals, Missed Appointments, Fees)
ii. Link to Clinic Policies page
g. Primary widget (displayed on all pages)
i. Hours of operation
ii. Contact Info
1. Tel
2. Fax
3. Email
4. Address
5. Get directions (link to Wayfind Maps)
2. Our Clinic
a. Main Page
i. Clinic Name
ii. Overview
iii. Languages Spoken
iv. Secondary Navigation
1. Mission
2. Services
3. Clinic Policies
4. Schedules (see attachment)
b. Our Clinic > Mission
c. Our Clinic > Services
i. For each service include service TITLE and DESCRIPTION
d. Our Clinic > Clinic Policies
i. For each policy include policy TITLE and DESCRIPTION
ii. Include the following policies in mockup
1. Late arrivals
2. Missed appointments
3. Fees for missed appointments
4. Referrals and follow-ups
5. Services not covered by RDA
6. Information for LTF patients
7. Medical Legal Reports
e. Our Clinic > Schedules
3. Our Staff
a. Main Page
i. Display a list of staff members. Include NAME and DESIGNATION
b. Our Staff > [Staff Name]
i. Include NAME, PICTURE, DESIGNATION, and BIO
4. Resources
a. Resources > Patient Health
i. Main Page
1. Posts (ordered by date)
a. Title
b. Summary
2. Side Navigation
a. Post Categories
ii. Patient Health > [post title]
1. Title
2. Post Category
3. Date
4. Author
5. Summary
6. Body
b. Resources > Links
1. Secondary Navigation - Categories
a. Sample Categories:
i. Local Services
ii. RDA and Drug Coverage
iii. Mental Health Resources
2. Category page
a. Include the following links in the 'Local Services' category
i. Hypertension clinics
ii. Home Care services
iii. Vaccine Clinics
c. Resources > Forms
i. Display a table with form TITLE and CATEGORY
ii. Side Navigation
1. Form Categories
a. Use the following sample Categories
i. Referrals
ii. Insurance
iii. Intake
iv. Discharge
v. Waivers
5. Alerts
a. Main page
i. List of all Alert posts
1. Include post TITLE as a link to the post
ii. Side Navigation
1. Alerts Archive
a. shown as Month + Number of posts
iii. Alerts > [Alert page]
1. Include TITLE, DATE, AUTHOR, BODY
6. Contact Us
a. Map
b. Hours of operation
c. Address
d. Phone number
e. Fax number
e. Fax number
f. Map
g. Email

Design notes:
- fixed width
- responsive (need designs for mobile, tablet, and desktop)
- simple, dark font, white background
- use Font Awesome icons where needed
- user adds own logo

Target Market(s)

Medical Clinics

Industry/Entity Type

Medical

Number of Pages Required

5+ page

Font styles to use
Serif
Sans Serif

Requirements
Must have
• Please keep designs very simple.
• Examples:
• https://www.quolbin.com/install
• http://www.ventrohax.com/company/about-us
• http://brindlequota.org/
• http://www.trosk.com/
Should not have
• Minimal or no use of shadows and gradients

```html
<!DOCTYPE html>
<html lang="en">
<head>
<meta charset="utf-8">
<title>Clinic Name — Home</title>
<link href="https://fonts.googleapis.com/css2?family=Questrial&family=Open+Sans:ital,wght@0,400;0,600;1,400&display=swap" rel="stylesheet">
<style>
:root{
  --ink:#1c1c1c;
  --text:#555555;
  --muted:#666666;
  --rule:#e6e6e6;
  --bg:#ffffff;
  --head:"Questrial", "Century Gothic", sans-serif;
  --body:"Open Sans", Arial, sans-serif;
}
*{box-sizing:border-box;margin:0;padding:0}
html,body{width:739px;height:1200px;overflow:hidden;background:var(--bg)}
body{position:relative;font-family:var(--body);color:var(--text)}
a{color:inherit;text-decoration:none}

.brand{position:absolute;left:50px;top:18px;font-family:var(--head);font-size:21px;letter-spacing:.2px;color:var(--ink)}
.top-links{position:absolute;right:46px;top:16px;display:flex;gap:17px;font-family:var(--head);font-size:8.5px;text-transform:uppercase;color:var(--ink)}
.top-links a{display:flex;align-items:center;gap:4px}
.top-links svg{width:8px;height:8px}

.side-nav{position:absolute;left:93px;top:82px;list-style:none;font-family:var(--head);font-size:11.5px;color:#333}
.side-nav li{height:25.6px}
.side-nav .current{color:#000;font-weight:600}

.main{position:absolute;left:212px;top:82px;width:315px}
.section{border-bottom:1px solid var(--rule);overflow:hidden}
.section h2{font-family:var(--head);font-weight:400;font-size:13.5px;line-height:17px;color:var(--ink);text-transform:uppercase;letter-spacing:.2px}
.new-patients{height:63px}
.new-patients p{margin-top:9px;font-size:9.6px}
.new-patients strong{color:var(--ink);font-weight:600}
.about{height:227px;padding-top:20px}
.about p{margin-top:4px;font-size:9.5px;line-height:18.25px}
.staff{height:328px;padding-top:20px}
.staff-list{list-style:none;margin-top:6px}
.staff-item{display:flex;height:48px;font-size:7.6px;line-height:12.7px}
.staff-item .who{width:110px}
.staff-item .name{font-weight:600;text-transform:uppercase;color:#333}
.staff-item .bio{width:205px}
.staff-item em{color:var(--ink)}
.btn{display:inline-block;border:1.2px solid #444;border-radius:2px;font-family:var(--head);font-size:7.8px;text-transform:uppercase;color:var(--ink);padding:4px 5px;letter-spacing:.2px}
.staff .btn{margin-top:-1px}
.alerts{height:249px;padding-top:20px}
.alert{margin-top:11px;font-size:7.6px;line-height:12.5px}
.alert + .alert{margin-top:23px}
.alert h3{font-family:var(--head);font-size:8px;font-weight:600;text-transform:uppercase;color:var(--ink);line-height:12px;margin-bottom:6px}
.policies{border:none;padding-top:20px}
.policies ul{list-style:none;margin-top:7px;font-family:var(--head);font-size:9px;text-transform:uppercase;color:var(--ink);line-height:17.3px}
.policies .btn{margin-top:17px}

.widget{position:absolute;left:544px;width:149px}
.widget h2{font-family:var(--head);font-weight:400;font-size:13.5px;color:var(--ink);text-transform:uppercase;margin-bottom:6px}
.hours{top:82px}
.contact{top:305px}
.info-row{display:flex;border-bottom:1px solid var(--rule);font-size:7.6px;line-height:12px;padding:6.3px 0}
.info-row dt{width:55px;font-family:var(--head);text-transform:uppercase;color:var(--ink);font-weight:600}
.info-row .sep{width:20px;color:var(--ink)}
.info-row dd{flex:1;white-space:nowrap}

.footer{position:absolute;left:212px;top:1150px;font-size:7.6px;line-height:12.5px;color:var(--muted)}
</style>
</head>
<body>

<div class="brand">CLINIC NAME</div>
<nav class="top-links">
  <a href="#"><svg viewBox="0 0 10 10"><rect x="1" y="2" width="8" height="7" fill="none" stroke="#555" stroke-width="1"/><line x1="1" y1="4" x2="9" y2="4" stroke="#555"/><line x1="3" y1="1" x2="3" y2="3" stroke="#555"/><line x1="7" y1="1" x2="7" y2="3" stroke="#555"/></svg>Book an Appointment</a>
  <a href="#"><svg viewBox="0 0 10 10"><circle cx="5" cy="5" r="3.2" fill="none" stroke="#555" stroke-width="1.6" stroke-dasharray="1.6 1"/><circle cx="5" cy="5" r="1.2" fill="#555"/></svg>Physician Toolbox</a>
</nav>

<ul class="side-nav">
  <li class="current">Home</li>
  <li>Our Clinic</li>
  <li>Our Staff</li>
  <li>Resources</li>
  <li>Alerts</li>
  <li>Contact Us</li>
</ul>

<main class="main">
  <section class="section new-patients">
    <h2>New Patients</h2>
    <p>Accepting new patients, <strong>CONTACT NOW!</strong></p>
  </section>

  <section class="section about">
    <h2>About Our Clinic</h2>
    <p>Lorem Ipsum is simply dummy text of the printing and typesetting industry. Lorem Ipsum has been the industry's standard dummy text ever since the 1500s, when an unknown printer took a galley of type and scrambled it to make a type specimen book. It has survived not only five centuries, but also the leap into electronic typesetting, re-maining essentially unchanged. It was popularised in the 1960s with the release of Tessary sheets containing Lorem Ipsum passages, and more recently with desktop publishing software like Quillmark Layout including versions of Lorem Ipsum.</p>
  </section>

  <section class="section staff">
    <h2>Our Staff</h2>
    <ul class="staff-list">
      <li class="staff-item"><div class="who"><div class="name">Dr. Owen Marsh, MD</div>Physician</div><div class="bio">In publishing and graphic design, lorem ipsum is a filler text a document or visual presentation...<em>[Read more]</em></div></li>
      <li class="staff-item"><div class="who"><div class="name">Dr. Lena Fairview, MD</div>Therapist</div><div class="bio">In publishing and graphic design, lorem ipsum is a filler text a document or visual presentation...<em>[Read more]</em></div></li>
      <li class="staff-item"><div class="who"><div class="name">Dr. Colm Ardley, MD</div>Radiologist</div><div class="bio">In publishing and graphic design, lorem ipsum is a filler text a document or visual presentation...<em>[Read more]</em></div></li>
      <li class="staff-item"><div class="who"><div class="name">Dr. Pruett, MD</div>Therapist</div><div class="bio">In publishing and graphic design, lorem ipsum is a filler text a document or visual presentation...<em>[Read more]</em></div></li>
      <li class="staff-item"><div class="who"><div class="name">Dr. Halvard, MD</div>Therapist</div><div class="bio">In publishing and graphic design, lorem ipsum is a filler text a document or visual presentation...<em>[Read more]</em></div></li>
    </ul>
    <a class="btn" href="#">View All Staff</a>
  </section>

  <section class="section alerts">
    <h2>Alerts</h2>
    <article class="alert">
      <h3>A handy lorem ipsum generator that helps to create dummy text<br>for all layout needs</h3>
      <p>In publishing and graphic design, lorem ipsum is a filler text commonly used to demonstrate the graphic elements of a document or visual presentation.Lorem ipsum dolor sit amet, consectetuer adipiscing elit, sed diam nonummy nibh euismod tincidunt ut laoreet dolore magna aliquam erat volutpat. Ut wisi enim ...</p>
    </article>
    <article class="alert">
      <h3>A handy lorem ipsum generator that helps to create dummy text<br>for all layout needs</h3>
      <p>In publishing and graphic design, lorem ipsum is a filler text commonly used to demonstrate the graphic elements of a document or visual presentation.Lorem ipsum dolor sit amet, consectetuer adipiscing elit, sed diam nonummy nibh euismod tincidunt ut laoreet dolore magna aliquam erat volutpat. Ut wisi enim ...</p>
    </article>
  </section>

  <section class="section policies">
    <h2>Clinic Policies</h2>
    <ul>
      <li>Late Arrivals</li>
      <li>Missed Appointments</li>
      <li>Fees</li>
    </ul>
    <a class="btn" href="#">View All Clinic Policies</a>
  </section>
</main>

<aside class="widget hours">
  <h2>Hours of Operation</h2>
  <dl>
    <div class="info-row"><dt>Monday</dt><span class="sep">:</span><dd>8:00am - 6:00pm</dd></div>
    <div class="info-row"><dt>Tuesday</dt><span class="sep">:</span><dd>8:00am - 6:00pm</dd></div>
    <div class="info-row"><dt>Wednesday</dt><span class="sep">:</span><dd>8:00am - 6:00pm</dd></div>
    <div class="info-row"><dt>Thursday</dt><span class="sep">:</span><dd>8:00am - 6:00pm</dd></div>
    <div class="info-row"><dt>Friday</dt><span class="sep">:</span><dd>8:00am - 6:00pm</dd></div>
    <div class="info-row"><dt>Saturday</dt><span class="sep">:</span><dd>9:00am - 4:00pm</dd></div>
    <div class="info-row"><dt>Sunday</dt><span class="sep">:</span><dd>9:00am - 4:00pm</dd></div>
  </dl>
</aside>

<aside class="widget contact">
  <h2>Contact Info</h2>
  <dl>
    <div class="info-row"><dt>Telephone</dt><span class="sep">:</span><dd>604 555 0182</dd></div>
    <div class="info-row"><dt>Fax</dt><span class="sep">:</span><dd>604 555 0182</dd></div>
    <div class="info-row"><dt>Email</dt><span class="sep">:</span><dd>hi@fernclinic.ca</dd></div>
    <div class="info-row"><dt>Address</dt><span class="sep">:</span><dd>48 Alder Row,<br>Fernvale, B.C,<br>Canada, V2K4R7</dd></div>
    <div class="info-row"><dt>Directions</dt><span class="sep">:</span><dd>Wayfind Maps</dd></div>
  </dl>
</aside>

<footer class="footer">
  <p>©2015 Clinic Name. All Rights Reserved</p>
  <p>Terms &amp; Privacy Policy | Sitemap</p>
</footer>

</body>
</html>
```